K7 Electrical Services Ltd Web design

I require a web site for my new electrical contracting company. We are customer service orientated. Offering high value electrical installations, design and maintenance. Focused on custom residential and commercial upgrading. Lighting design and application are paramount in our company's services. Industry leading product use and integration are always on the forefront with our customer client services. As well as energy efficiency.

Target Market(s)

Homebuilders, General Contractors, Property management companies, clients, individuals,

Industry/Entity Type

Electric Company

Coding

Coded - Design and coding required

Number of Pages Required

3 page

Requirements
Must have
• Classic, modern, edgy but not trendy . Appeals to the masse.
• 3 page
• home page
• about page
• gallery page
• ability to contact from the webiste
Nice to have
• open to all types of designs that are relative to the construction industry.
• Black, Grey, metallic ice blue and deep purple colours from the logo.
Should not have
• anything cheesy with cartoon light bulb images.

```html
<!DOCTYPE html>
<html lang="en">
<head>
<meta charset="utf-8">
<title>K7 Electrical Services Ltd</title>
<link href="https://fonts.googleapis.com/css2?family=Poppins:wght@400;500;600;700&family=Open+Sans:ital,wght@0,400;1,400&display=swap" rel="stylesheet">
<style>
:root{
  --purple:#5a2a82;
  --purple-deep:#4a1f6e;
  --purple-soft:#7a4aa3;
  --ink:#1d1d1f;
  --body:#6a6a6a;
  --grey-bg:#f2f2f2;
  --footer:#2b2b2b;
  --footer-bottom:#1c1c1c;
  --white:#fff;
  --gold:#e8b500;
}
*{margin:0;padding:0;box-sizing:border-box}
html,body{width:1200px;height:3261px;overflow:hidden}
body{position:relative;background:var(--white);font-family:'Poppins',sans-serif;color:var(--ink)}
.abs{position:absolute}
.center{text-align:center}

/* top bar + header */
.topbar{left:641px;top:0;width:559px;height:33px;background:var(--purple);clip-path:polygon(28px 0,100% 0,100% 100%,0 100%);display:flex;align-items:center;gap:34px;padding-left:54px;color:var(--white);font-size:13px}
.topbar span{display:flex;align-items:center;gap:10px}
.brand{left:98px;top:10px;width:260px;color:var(--purple);font-weight:600;line-height:1;text-align:center}
.brand .mark{font-size:52px;letter-spacing:2px}
.brand .line1{font-size:29px;letter-spacing:1px;margin-top:2px}
.brand .line2{font-size:13px;letter-spacing:5px;margin-top:4px}
.nav{left:435px;top:68px;display:flex;gap:0;font-size:17px;font-weight:400}
.nav a{color:var(--ink);text-decoration:none;margin-right:44px}
.nav a.active{color:var(--purple)}

/* hero */
.hero{left:0;top:120px;width:1200px;height:467px;background:linear-gradient(110deg,#5b5f63 0%,#8a8d8f 35%,#6b6e70 60%,#3c3f42 100%)}
.hero-title{left:0;top:245px;width:1200px;color:var(--white);font-size:52px;font-weight:500;letter-spacing:1px}
.hero-sub{left:0;top:316px;width:1200px;color:var(--white);font-size:28px;font-weight:500}
.btn-hero{left:496px;top:370px;width:208px;height:56px;border:2px solid var(--white);border-radius:28px;background:var(--purple);color:var(--white);font-size:18px;font-weight:500;display:flex;align-items:center;justify-content:center}
.hero-arrow{top:318px}
.badge{left:552px;top:539px;width:96px;height:96px;border-radius:50%;background:var(--white);box-shadow:0 2px 6px rgba(0,0,0,.15);display:flex;align-items:center;justify-content:center;color:var(--purple);font-weight:600;font-size:34px}

/* headings & text */
.h2{left:0;width:1200px;font-size:36px;font-weight:600;text-align:center}
.lead{font-family:'Open Sans',sans-serif;font-size:14.5px;line-height:26px;color:var(--body);text-align:center}
.btn-solid{background:var(--purple);color:var(--white);border-radius:22px;font-size:14px;font-weight:600;display:flex;align-items:center;justify-content:center}
.btn-outline{border:2px solid var(--purple);color:var(--purple);border-radius:24px;font-size:14px;font-weight:600;display:flex;align-items:center;justify-content:center;background:var(--white)}

/* services */
.services{left:0;top:970px;width:1200px;height:526px;background:var(--grey-bg)}
.card{top:1135px;width:298px;height:280px;border:1px solid var(--purple-soft);background:var(--white)}
.card .photo{height:217px}
.card .label{height:62px;display:flex;align-items:center}
.card .icon{width:72px;height:62px;background:var(--purple);display:flex;align-items:center;justify-content:center}
.card .name{padding-left:16px;font-size:21px;font-weight:500}

/* why */
.why{left:0;top:1496px;width:1200px;height:434px;background:linear-gradient(90deg,var(--purple-deep),#6b3a95 55%,var(--purple) 100%)}
.why-title{left:100px;top:1604px;color:var(--white);font-size:36px;font-weight:600}
.why-text{left:100px;width:520px;color:var(--white);font-family:'Open Sans',sans-serif;font-size:15px;line-height:24px}
.feature{left:657px;width:420px;color:var(--white)}
.feature h3{font-size:18px;font-weight:600;display:flex;align-items:center;gap:12px}
.feature p{font-family:'Open Sans',sans-serif;font-size:12px;line-height:18px;padding-left:0;margin-top:6px}

/* projects */
.project{top:2144px;width:245px;height:226px}

/* testimonials */
.testimonials{left:0;top:2535px;width:1200px;height:367px;background:var(--grey-bg)}
.avatar{left:232px;top:2665px;width:144px;height:144px;border-radius:50%;border:2px solid var(--purple-soft);padding:6px;background:var(--white)}
.avatar div{width:100%;height:100%;border-radius:50%;background:linear-gradient(160deg,#d8dde2,#9aa6b0)}
.quote{left:404px;top:2700px;width:560px;font-family:'Open Sans',sans-serif;font-style:italic;font-size:15px;line-height:24px;color:#555}
.author{left:600px;top:2775px;width:357px;text-align:right;color:var(--purple);font-family:'Open Sans',sans-serif;font-style:italic;font-size:17px}
.stars{left:877px;top:2808px;color:var(--gold);font-size:14px;letter-spacing:1px}

/* footer */
.footer{left:0;top:2902px;width:1200px;height:294px;background:var(--footer)}
.footer-bottom{left:0;top:3196px;width:1200px;height:65px;background:var(--footer-bottom);color:#cfcfcf;font-size:13px;display:flex;align-items:center;justify-content:center}
.footer-brand{left:100px;top:2957px;width:200px;color:var(--white);font-weight:600;text-align:center;line-height:1}
.footer-brand .mark{font-size:40px;letter-spacing:2px}
.footer-brand .line1{font-size:23px;margin-top:2px}
.footer-brand .line2{font-size:10px;letter-spacing:4px;margin-top:3px}
.social{top:3063px;width:48px;height:48px;border-radius:50%;background:var(--white)}
.fcol{top:2957px;color:var(--white)}
.fcol h4{font-size:17px;font-weight:500;letter-spacing:1px;margin-bottom:18px}
.fcol ul{list-style:none;font-family:'Open Sans',sans-serif;font-size:13px;line-height:27px;color:#dcdcdc}
.field{left:789px;width:311px;color:var(--white);font-family:'Open Sans',sans-serif;font-size:13px;border-bottom:1px solid #bdbdbd;padding-bottom:4px}
.btn-submit{left:791px;top:3091px;width:114px;height:37px;border:2px solid var(--white);border-radius:19px;color:var(--white);font-size:14px;font-weight:600;display:flex;align-items:center;justify-content:center}
</style>
</head>
<body>

<!-- Header -->
<div class="abs topbar">
  <span><svg width="14" height="14" viewBox="0 0 24 24" fill="none" stroke="#fff" stroke-width="2"><path d="M5 3h4l2 5-3 2a12 12 0 0 0 6 6l2-3 5 2v4a2 2 0 0 1-2 2A18 18 0 0 1 3 5a2 2 0 0 1 2-2z"/></svg>+1 555 014 2270</span>
  <span><svg width="16" height="12" viewBox="0 0 24 18" fill="none" stroke="#fff" stroke-width="2"><rect x="1" y="1" width="22" height="16"/><path d="M1 1l11 9 11-9"/></svg>info@k7electrical.com</span>
</div>
<div class="abs brand">
  <div class="mark">K7</div>
  <div class="line1">ELECTRICAL</div>
  <div class="line2">SERVICES</div>
</div>
<nav class="abs nav">
  <a class="active">Home</a><a>About Us</a><a>Our Team</a><a>Services</a><a>News</a><a>Contact</a>
  <svg width="16" height="16" viewBox="0 0 24 24" fill="none" stroke="#1d1d1f" stroke-width="3" style="margin-top:4px"><circle cx="10" cy="10" r="7"/><path d="M15 15l7 7"/></svg>
</nav>

<!-- Hero -->
<div class="abs hero" role="img" aria-label="Photo of three electricians in hard hats inspecting a high-voltage panel"></div>
<div class="abs hero-title center">K7 ELECTRICAL SERVICES</div>
<div class="abs hero-sub center">We Do Lighting Design &amp; Application</div>
<div class="abs btn-hero">LEARN MORE</div>
<svg class="abs hero-arrow" style="left:32px" width="24" height="70" viewBox="0 0 24 70" fill="none" stroke="#fff" stroke-width="3"><path d="M22 2L2 35l20 33"/></svg>
<svg class="abs hero-arrow" style="left:1134px" width="24" height="70" viewBox="0 0 24 70" fill="none" stroke="#fff" stroke-width="3"><path d="M2 2l20 33L2 68"/></svg>
<div class="abs badge">K7</div>

<!-- Welcome -->
<h2 class="abs h2" style="top:688px">WELCOME TO K7 ELECTRICAL SERVICES</h2>
<p class="abs lead" style="left:148px;top:746px;width:906px">Vestibulum lectus nibh, consectetur nec nunc non, scelerisque vulputate nunc. Praesent ac purus turpis. Curabitur congue ex sem, sit amet scelerisque nisi convallis non. Vivamus rutrum imperdiet sodales. Vivamus ante sapien, laoreet at elementum id, suscipit vitae augue. Phasellus eget leo accumsan, tristique orci sed, elementum lectus.</p>
<div class="abs btn-solid" style="left:522px;top:843px;width:154px;height:40px">READ MORE</div>

<!-- Services -->
<section class="abs services"></section>
<h2 class="abs h2" style="top:1044px">OUR SERVICES</h2>
<div class="abs card" style="left:98px">
  <div class="photo" role="img" aria-label="Photo of an electrician installing a wall-mounted light fixture" style="background:linear-gradient(135deg,#a0553f,#2a5aa8 70%,#e2c230)"></div>
  <div class="label"><div class="icon"><svg width="30" height="34" viewBox="0 0 30 34" fill="none" stroke="#fff" stroke-width="2"><circle cx="15" cy="13" r="10"/><circle cx="15" cy="13" r="5"/><path d="M11 26h8M12 30h6"/></svg></div><div class="name">Installation</div></div>
</div>
<div class="abs card" style="left:452px">
  <div class="photo" role="img" aria-label="Photo of rolled electrical blueprints" style="background:linear-gradient(135deg,#c9d6e8,#eef2f8 60%,#9fb3cf)"></div>
  <div class="label"><div class="icon"><svg width="32" height="30" viewBox="0 0 32 30" fill="#fff"><rect x="2" y="20" width="4" height="8"/><rect x="9" y="15" width="4" height="13"/><rect x="16" y="10" width="4" height="18"/><rect x="23" y="4" width="4" height="24"/></svg></div><div class="name">Electrical Design</div></div>
</div>
<div class="abs card" style="left:802px">
  <div class="photo" role="img" aria-label="Photo of an electrician servicing a wiring cabinet" style="background:linear-gradient(135deg,#c8c8c8,#3a4a6a 55%,#d8c23a)"></div>
  <div class="label"><div class="icon"><svg width="32" height="32" viewBox="0 0 32 32" fill="none" stroke="#fff" stroke-width="2.5"><path d="M5 16a11 11 0 0 1 19-7M27 16a11 11 0 0 1-19 7"/><path d="M24 3v6h-6M8 29v-6h6"/><path d="M17 10l-4 7h6l-4 6" stroke-width="2"/></svg></div><div class="name">Maintenance</div></div>
</div>

<!-- Why choose us -->
<section class="abs why" role="img" aria-label="Purple band over a faint photo of electrical plans and tools"></section>
<h2 class="abs why-title">WHY CHOOSE US</h2>
<p class="abs why-text" style="top:1663px">Vestibulum lectus nibh, consectetur nec nunc non, scelerisque vulputate nunc. Praesent ac purus turpis. Curabitur congue ex sem, sit amet elerisque nisi convallis non.</p>
<p class="abs why-text" style="top:1750px">Vivamus rutrum imperdiet sodales. Vivamus ante sapien, laoreet at elementum id, suscipit vitae augue. Phasellus eget leo accumsan, tristique orci sed, elementum lectus.</p>
<div class="abs feature" style="top:1592px">
  <h3><svg width="22" height="28" viewBox="0 0 22 28" fill="#fff"><path d="M3 9a8 8 0 0 1 16 0z"/><circle cx="11" cy="13" r="4"/><path d="M2 28v-5a9 6 0 0 1 18 0v5z"/></svg>We Are Professionals</h3>
  <p>Praesent ac purus turpis. Curabitur congue ex sem, sit amet<br>scelerisque nisi convallis nonum lectus.</p>
</div>
<div class="abs feature" style="top:1686px">
  <h3><svg width="24" height="24" viewBox="0 0 24 24" fill="#fff"><rect x="1" y="10" width="5" height="13"/><path d="M8 10l5-8c2 0 3 1 2 4l-1 4h7c2 0 3 2 2 4l-3 8H8z"/></svg>We Are Trusted</h3>
  <p>Praesent ac purus turpis. Curabitur congue ex sem, sit amet<br>scelerisque nisi convallis nonum lectus.</p>
</div>
<div class="abs feature" style="top:1780px">
  <h3><svg width="24" height="24" viewBox="0 0 24 24" fill="#fff"><path d="M12 1l3.4 7 7.6 1-5.5 5.3 1.3 7.7L12 18.3 5.2 22l1.3-7.7L1 9l7.6-1z"/></svg>We Are Experts</h3>
  <p>Praesent ac purus turpis. Curabitur congue ex sem, sit amet<br>scelerisque nisi convallis nonum lectus.</p>
</div>

<!-- Projects -->
<h2 class="abs h2" style="top:2007px">OUR LATEST PROJECTS</h2>
<p class="abs lead" style="left:200px;top:2066px;width:800px">Vestibulum lectus nibh, consectetur nec nunc non, scelerisque vulputate nunc. Praesent ac purus turpis. Curabitur congue ex sem, sit amet scelerisque nisi convallis non. Vivamus rutrum imperdiet sodales.</p>
<div class="abs project" role="img" aria-label="Photo of solar panels under a purple overlay" style="left:98px;background:linear-gradient(160deg,#7a4aa3,#5a2a82)"></div>
<svg class="abs" style="left:201px;top:2237px" width="40" height="40" viewBox="0 0 24 24" fill="none" stroke="#fff" stroke-width="2.5" stroke-linecap="round"><path d="M10 14a4 4 0 0 0 6 0l4-4a4 4 0 0 0-6-6l-1 1"/><path d="M14 10a4 4 0 0 0-6 0l-4 4a4 4 0 0 0 6 6l1-1"/></svg>
<div class="abs project" role="img" aria-label="Photo of technicians servicing an outdoor air-conditioning unit" style="left:352px;background:linear-gradient(135deg,#c9c2b0,#6b6f72 55%,#d6b23a)"></div>
<div class="abs project" role="img" aria-label="Photo of an engineer checking a meter cabinet" style="left:604px;background:linear-gradient(135deg,#d8d8d8,#8a8f95 50%,#d7c43c)"></div>
<div class="abs project" role="img" aria-label="Photo of electrician tools on a desk with plans" style="left:857px;background:linear-gradient(135deg,#e4e1dc,#2f4f9a 60%,#c8a06a)"></div>
<div class="abs btn-outline" style="left:528px;top:2407px;width:142px;height:45px">VIEW ALL</div>

<!-- Testimonials -->
<section class="abs testimonials"></section>
<h2 class="abs h2" style="top:2603px">TESTIMONIALS</h2>
<svg class="abs" style="left:98px;top:2717px" width="16" height="40" viewBox="0 0 16 40" fill="none" stroke="#555" stroke-width="2"><path d="M14 2L2 20l12 18"/></svg>
<svg class="abs" style="left:1080px;top:2717px" width="16" height="40" viewBox="0 0 16 40" fill="none" stroke="#555" stroke-width="2"><path d="M2 2l12 18L2 38"/></svg>
<div class="abs avatar"><div role="img" aria-label="Portrait photo of the client"></div></div>
<p class="abs quote">Praesent ac purus turpis. Curabitur congue ex sem, sit amet scelerisque nisi convallis non. Vivamus rutrum imperdiet sodales. Vivamus ante sapien, laoreet at elementum id, suscipit vitae augue.</p>
<div class="abs author">Marina Delcourt</div>
<div class="abs stars">★★★★☆</div>

<!-- Footer -->
<footer class="abs footer"></footer>
<div class="abs footer-brand">
  <div class="mark">K7</div>
  <div class="line1">ELECTRICAL</div>
  <div class="line2">SERVICES</div>
</div>
<div class="abs social" style="left:98px"></div>
<div class="abs social" style="left:156px"></div>
<div class="abs social" style="left:213px"></div>
<div class="abs social" style="left:267px"></div>
<div class="abs fcol" style="left:380px">
  <h4>QUICK LINKS</h4>
  <ul><li>Home</li><li>About Us</li><li>Our Team</li><li>Services</li><li>News</li><li>Contact</li></ul>
</div>
<div class="abs fcol" style="left:572px">
  <h4>SUPPORT US</h4>
  <ul><li>Privacy Policy</li><li>Copyright &amp; Disclaimer</li><li>Terms &amp; Conditions</li></ul>
</div>
<div class="abs fcol" style="left:789px">
  <h4>STAY IN TOUCH</h4>
</div>
<div class="abs field" style="top:3007px">Name</div>
<div class="abs field" style="top:3049px">Email</div>
<div class="abs btn-submit">SUBMIT</div>
<div class="abs footer-bottom">Copyright © 2018. All Rights Reserved.</div>

</body>
</html>
```